Modern Business Card for Larkwell 2018

Our company assumes the best about people. We are creating an online community of entrepreneurs and business leaders who struggle with marketing their business online.

This business card should POP! We recently got a new logo and are launching a new website next month, so our business cards should make a statement that feels:
-Fresh
-Smart
-Trustworthy
-Fun

Target Market(s)

small business owners, entrepreneurs

Industry/Entity Type

Digital Marketing

Contact Information for Business Card

Dimensions: 3.5" x 2"

Font styles to use
Sans Serif

Colors
f37122
ffffff

Requirements
Must have
• We need a business card with a modern, bold design. We will use one side of the card as a lead-generation offer, so text on one side will need to fit up to 140 characters. The business card should stick to our core colors (orange, black, and white).
Nice to have
• We think a vertical "portrait" design could be interesting.
Should not have
• Should not look like a traditional business card. The round icon should stand out from a distance.

```html
<!DOCTYPE html>
<html lang="en">
<head>
<meta charset="utf-8">
<title>Larkwell Business Card</title>
<link href="https://fonts.googleapis.com/css2?family=Open+Sans:wght@400;600;700;800&display=swap" rel="stylesheet">
<style>
  :root {
    --orange: #f37122;
    --white: #ffffff;
    --ink: #1e1e1e;
    --grey-text: #555555;
    --panel: #e6e6e6;
    --rule: #c9c9c9;
    --stage: #ecebe8;
  }
  * { box-sizing: border-box; margin: 0; padding: 0; }
  html, body {
    width: 1200px; height: 960px; overflow: hidden;
    background: var(--stage);
    font-family: "Open Sans", Arial, sans-serif;
  }
  .card {
    position: absolute; left: 250px;
    width: 700px; height: 400px;
    overflow: hidden;
    box-shadow: 0 6px 18px rgba(0,0,0,0.18);
  }

  /* ---------- Offer side ---------- */
  .card-offer { top: 50px; background: var(--orange); }
  .offer-mark {
    position: absolute; left: 24px; top: 40px; width: 260px; height: 200px;
    display: flex; align-items: center; justify-content: center; gap: 10px;
  }
  .offer-mark .dot {
    width: 26px; height: 26px; border-radius: 50%; background: var(--white); flex: none;
  }
  .offer-mark .brand {
    color: var(--white); font-weight: 800; font-size: 34px; letter-spacing: 1px; line-height: 1;
  }
  .offer-divider {
    position: absolute; left: 300px; top: 40px; width: 1px; height: 200px;
    background: rgba(255,255,255,0.35);
  }
  .offer-copy { position: absolute; left: 332px; top: 42px; width: 340px; color: var(--white); }
  .offer-headline {
    font-weight: 800; font-size: 24px; line-height: 1.05; text-transform: uppercase;
    color: #fde3d2;
  }
  .offer-body { margin-top: 10px; font-size: 17px; line-height: 1.25; color: #fbd3ba; }
  .offer-url { margin-top: 10px; font-weight: 700; font-size: 21px; }
  .write-panel {
    position: absolute; left: 28px; right: 28px; top: 262px; height: 96px;
    background: var(--panel); border-radius: 18px;
    padding: 26px 40px 0 40px;
  }
  .write-panel .line { height: 1px; background: #555; margin-bottom: 30px; }

  /* ---------- Contact side ---------- */
  .card-contact { top: 510px; background: var(--white); }
  .logo-block {
    position: absolute; left: 36px; top: 140px; width: 316px;
    display: flex; flex-direction: column; align-items: center;
  }
  .logo-row { display: flex; align-items: center; gap: 10px; }
  .logo-row .dot {
    width: 24px; height: 24px; border-radius: 50%; background: var(--orange); flex: none;
  }
  .logo-row .brand {
    font-weight: 800; font-size: 44px; letter-spacing: 1px; color: var(--ink); line-height: 1;
  }
  .logo-block .tagline {
    margin-top: 10px; font-weight: 600; font-size: 12.5px; letter-spacing: 1.2px;
    text-transform: uppercase; color: var(--ink);
  }
  .contact-divider {
    position: absolute; left: 362px; top: 92px; width: 1px; height: 160px;
    background: var(--rule);
  }
  .contact-info { position: absolute; left: 392px; top: 150px; }
  .contact-name {
    font-weight: 800; font-size: 27px; color: var(--orange); text-transform: uppercase; line-height: 1.1;
  }
  .contact-role {
    font-weight: 700; font-size: 19px; color: var(--ink); text-transform: uppercase; line-height: 1.25;
  }
  .contact-email { font-size: 18px; color: var(--grey-text); line-height: 1.25; }
  .edge-band { position: absolute; left: 0; bottom: 0; width: 700px; height: 36px; }
</style>
</head>
<body>

<section class="card card-offer" aria-label="Offer side">
  <div class="offer-mark">
    <div class="dot"></div>
    <div class="brand">LARKWELL</div>
  </div>
  <div class="offer-divider"></div>
  <div class="offer-copy">
    <p class="offer-headline">Reach more people.<br>Make more money.<br>Create more impact.</p>
    <p class="offer-body">Get your free Larkwell<br>Starter Package and our<br>marketing guide today at</p>
    <p class="offer-url">Larkwellnow.com/start</p>
  </div>
  <div class="write-panel">
    <div class="line"></div>
    <div class="line"></div>
  </div>
</section>

<section class="card card-contact" aria-label="Contact side">
  <div class="logo-block">
    <div class="logo-row">
      <div class="dot"></div>
      <div class="brand">LARKWELL</div>
    </div>
    <div class="tagline">Share ideas that move people</div>
  </div>
  <div class="contact-divider"></div>
  <div class="contact-info">
    <p class="contact-name">Dana Whitfield</p>
    <p class="contact-role">Story Marketing Coach</p>
    <p class="contact-email">dana@larkwellnow.com</p>
  </div>
  <svg class="edge-band" viewBox="0 0 700 36" aria-hidden="true">
    <polygon points="0,0 395,14 415,36 0,36" fill="var(--orange)"/>
    <polygon points="395,14 700,22 700,36 415,36" fill="var(--ink)"/>
  </svg>
</section>

</body>
</html>
```